Martin R Cole DDS (dentist) needs a business card/business logo design

I would like an eye-catchingly conservative or elegant graphic presentation of my business name with the elements: prevention, restoration, and cosmetics (these are the services I'd like to emphasize) .
The business card would have room for address lines, phone and fax, web address. No standard teeth or oral representations please. Should communicate professionalism. Whatever color scheme works.

Thank you

Target Market(s)

I just want a good looking business card

Industry/Entity Type

Conservative

Contact Information for Business Card

Adress: 4163 Brisdale Ave Lakewood CA 90648 Phone: 562 419 3086 FAX 562 419 5274 Web: Fernhilldental.com

Font styles to use
Sans Serif

Colors
0255a3

Requirements
Must have
• business name with the elements: prevention, restoration, and cosmetics (these are the services I'd like to emphasize)
• communicates professionalism
Nice to have
• eye catching but not flashy graphics
Should not have
• no pictures of teeth or dental instruments

```html
<!DOCTYPE html>
<html lang="en">
<head>
<meta charset="utf-8">
<title>Martin R Cole DDS — Business Card</title>
<link rel="stylesheet" href="https://fonts.googleapis.com/css2?family=Ubuntu:wght@400;500;700&display=swap">
<style>
  :root {
    --brand-blue: #0255a3;
    --card-white: #ffffff;
    --backdrop: #e9ecef;
    --ink: #0255a3;
  }
  * { margin: 0; padding: 0; box-sizing: border-box; }
  html, body {
    width: 1200px; height: 1000px; overflow: hidden;
    background: var(--backdrop);
    font-family: "Ubuntu", sans-serif;
  }
  .business-card {
    position: absolute; left: 75px; top: 200px;
    width: 1050px; height: 600px;
    background: var(--card-white);
    overflow: hidden;
    box-shadow: 0 6px 24px rgba(0,0,0,0.12);
  }
  .card-graphics { position: absolute; inset: 0; }
  .name-block {
    position: absolute; left: 112px; top: 108px;
    width: 320px; color: var(--card-white);
  }
  .doctor-name { font-weight: 700; font-size: 34px; line-height: 1; white-space: nowrap; }
  .doctor-title { font-weight: 400; font-size: 26px; text-align: right; margin-top: 8px; padding-right: 10px; }
  .services-tagline {
    position: absolute; right: 22px; top: 158px;
    color: var(--ink); font-weight: 500; font-size: 27px; white-space: nowrap;
  }
  .contact-line {
    position: absolute; display: flex; align-items: center; gap: 8px;
    color: var(--ink); font-weight: 500; font-size: 26px; white-space: nowrap;
  }
  .contact-line svg { flex: none; }
  .phone-line { left: 40px; top: 262px; }
  .fax-line { left: 40px; top: 312px; }
  .web-line { left: 370px; top: 378px; }
  .address-line { left: 370px; top: 428px; font-weight: 700; }
</style>
</head>
<body>
  <article class="business-card">
    <svg class="card-graphics" width="1050" height="600" viewBox="0 0 1050 600">
      <!-- edge tab -->
      <rect x="0" y="88" width="26" height="96" fill="var(--brand-blue)"/>
      <!-- person icon -->
      <g fill="var(--brand-blue)">
        <circle cx="62" cy="110" r="15"/>
        <path d="M38 168 Q38 132 62 132 Q86 132 86 168 Z"/>
        <path d="M60 134 L64 134 L66 156 L62 162 L58 156 Z" fill="var(--card-white)"/>
      </g>
      <!-- name pill -->
      <path d="M100 98 H390 A48 48 0 0 1 438 146 A48 48 0 0 1 390 194 H100 Z" fill="var(--brand-blue)"/>
      <!-- tagline rule -->
      <rect x="420" y="204" width="630" height="5" fill="var(--brand-blue)"/>
      <!-- bottom bands -->
      <path d="M0 478 L720 532 L720 538 L0 486 Z" fill="var(--brand-blue)"/>
      <path d="M0 500 L640 550 Q690 556 712 548 Q740 534 780 534 L1050 534 L1050 600 L0 600 Z" fill="var(--brand-blue)"/>
    </svg>

    <div class="name-block">
      <div class="doctor-name">Martin R Cole DDS</div>
      <div class="doctor-title">Dentist</div>
    </div>

    <div class="services-tagline">Prevention, Restoration and Cosmetics</div>

    <div class="contact-line phone-line">
      <svg width="28" height="24" viewBox="0 0 28 24" fill="var(--brand-blue)"><path d="M2 8 Q14 0 26 8 L24 12 L19 10 L19 7 Q14 5 9 7 L9 10 L4 12 Z"/><path d="M6 13 H22 L24 22 H4 Z"/><circle cx="14" cy="17" r="3" fill="#fff"/></svg>
      <span>: 562- 419- 3086</span>
    </div>
    <div class="contact-line fax-line">
      <svg width="28" height="26" viewBox="0 0 28 26" fill="var(--brand-blue)"><rect x="7" y="1" width="14" height="8"/><rect x="1" y="9" width="26" height="11" rx="2"/><rect x="7" y="15" width="14" height="10" fill="#fff" stroke="var(--brand-blue)" stroke-width="2"/></svg>
      <span>: 562- 419- 5274</span>
    </div>
    <div class="contact-line web-line">
      <svg width="30" height="30" viewBox="0 0 30 30"><circle cx="15" cy="15" r="13" fill="var(--brand-blue)"/><rect x="3" y="11" width="24" height="8" fill="#fff"/><rect x="6" y="13" width="18" height="4" fill="var(--brand-blue)"/></svg>
      <span>: www.Fernhilldental.com</span>
    </div>
    <div class="contact-line address-line">
      <svg width="32" height="30" viewBox="0 0 32 30"><path d="M3 18 H11 M21 18 H29 L31 28 H1 Z" fill="none" stroke="var(--brand-blue)" stroke-width="2"/><path d="M16 22 C10 15 9 12 9 9 A7 7 0 0 1 23 9 C23 12 22 15 16 22 Z" fill="var(--brand-blue)"/><circle cx="16" cy="9" r="2.5" fill="#fff"/></svg>
      <span>: 4163 Brisdale Ave, Lakewood, CA 90648</span>
    </div>
  </article>
</body>
</html>
```